Moravel Aesthetic Doctor

I require an elegant, luxurious looking business card for my aesthetic business. I am a doctor and that will set me aside from competitors. I am planning to provide home and spa based treatments to clients with high expectations. I have attached my logo.

```html
<!DOCTYPE html>
<html lang="en">
<head>
<meta charset="utf-8">
<title>Moravel Aesthetic Doctor – Business Card</title>
<link href="https://fonts.googleapis.com/css2?family=Work+Sans:wght@400;500;600&display=swap" rel="stylesheet">
<style>
  :root {
    --stage: #1c1c1d;
    --card-dark: #3a3a3d;
    --card-white: #ffffff;
    --accent: #1aa3e8;
    --ink: #2f2f33;
    --ink-light: #f2f2f2;
    --swoosh: #3b3b3e;
  }
  * { margin: 0; padding: 0; box-sizing: border-box; }
  html, body { width: 1200px; height: 930px; overflow: hidden; }
  body {
    background: var(--stage);
    font-family: "Work Sans", sans-serif;
    position: relative;
  }
  .card {
    position: absolute;
    width: 560px;
    height: 330px;
    border-radius: 18px;
    overflow: hidden;
  }
  .card--back {
    left: 60px; top: 80px;
    background: var(--card-dark);
    color: var(--ink-light);
  }
  .card--front {
    left: 580px; top: 520px;
    background: var(--card-white);
    color: var(--ink);
  }
  .brand {
    display: flex;
    align-items: center;
    gap: 12px;
  }
  .brand__dot {
    width: 34px; height: 34px;
    border-radius: 50%;
    background: var(--accent);
    flex: none;
  }
  .brand__name {
    font-weight: 500;
    font-size: 22px;
    letter-spacing: 1.5px;
    text-transform: uppercase;
    line-height: 1.2;
  }
  .card--back .brand {
    position: absolute;
    left: 0; right: 0; top: 92px;
    justify-content: center;
  }
  .card--back .brand__name { color: var(--ink-light); }
  .services {
    position: absolute;
    left: 0; right: 0; top: 178px;
    text-align: center;
    font-size: 15px;
    line-height: 1.55;
    letter-spacing: 0.5px;
  }
  .services__sep { color: var(--accent); padding: 0 4px; }
  .services__tag { text-transform: uppercase; letter-spacing: 1px; }

  .card--front .brand {
    position: absolute;
    left: 36px; top: 118px;
    width: 220px;
  }
  .card--front .brand__name { color: var(--accent); font-size: 19px; }
  .divider {
    position: absolute;
    left: 272px; top: 56px;
    width: 1.5px; height: 150px;
    background: var(--accent);
  }
  .contact {
    position: absolute;
    left: 296px; top: 52px;
    font-size: 14px;
    line-height: 1.5;
  }
  .contact__name { color: var(--accent); font-weight: 600; font-size: 16px; }
  .contact__row { display: flex; align-items: center; gap: 7px; }
  .contact__row svg { width: 12px; height: 12px; fill: var(--accent); flex: none; }
  .swoosh { position: absolute; left: 0; bottom: 0; width: 560px; height: 130px; }
</style>
</head>
<body>
  <section class="card card--back" aria-label="Card back">
    <div class="brand">
      <span class="brand__dot"></span>
      <span class="brand__name">Moravel Aesthetic Doctor</span>
    </div>
    <p class="services">
      Dermal injectables<span class="services__sep">|</span>Plasma facials<span class="services__sep">|</span>Microneedling<br>
      Skin boosters<span class="services__sep">|</span>Excessive sweating<br>
      <span class="services__tag">Home and spa based treatments</span>
    </p>
  </section>

  <section class="card card--front" aria-label="Card front">
    <div class="brand">
      <span class="brand__dot"></span>
      <span class="brand__name">Moravel Aesthetic Doctor</span>
    </div>
    <div class="divider"></div>
    <div class="contact">
      <p class="contact__name">Dr Lena Vossberg MRCPCH MD</p>
      <p>Australasian Diploma<br>of Aesthetic Medicine</p>
      <p class="contact__row"><svg viewBox="0 0 24 24"><path d="M6.6 10.8a15 15 0 0 0 6.6 6.6l2.2-2.2a1 1 0 0 1 1-.25 11.4 11.4 0 0 0 3.6.57 1 1 0 0 1 1 1V20a1 1 0 0 1-1 1A17 17 0 0 1 3 4a1 1 0 0 1 1-1h3.5a1 1 0 0 1 1 1c0 1.25.2 2.45.57 3.57a1 1 0 0 1-.25 1z"/></svg>0800 555 014</p>
      <p class="contact__row"><svg viewBox="0 0 24 24"><path d="M2 5h20v14H2zm2 2v.5l8 5 8-5V7zm0 2.8V17h16V9.8l-8 5z"/></svg>lena@moravel.co.nz</p>
      <p class="contact__row"><svg viewBox="0 0 24 24"><path d="M12 2a10 10 0 1 0 0 20 10 10 0 0 0 0-20zm6.9 6h-3a15 15 0 0 0-1.3-3.9A8 8 0 0 1 18.9 8zM12 4a13 13 0 0 1 1.9 4h-3.8A13 13 0 0 1 12 4zM4.3 14a8 8 0 0 1 0-4h3.4a16 16 0 0 0 0 4zm.8 2h3a15 15 0 0 0 1.3 3.9A8 8 0 0 1 5.1 16zM8 8H5.1a8 8 0 0 1 4.3-3.9A15 15 0 0 0 8 8zm4 12a13 13 0 0 1-1.9-4h3.8A13 13 0 0 1 12 20zm2.3-6H9.7a14 14 0 0 1 0-4h4.6a14 14 0 0 1 0 4zm.3 5.9a15 15 0 0 0 1.3-3.9h3a8 8 0 0 1-4.3 3.9zm1.7-5.9a16 16 0 0 0 0-4h3.4a8 8 0 0 1 0 4z"/></svg>www.moravel.co.nz</p>
    </div>
    <svg class="swoosh" viewBox="0 0 560 130" preserveAspectRatio="none" aria-hidden="true">
      <path d="M0 90 C180 70 380 40 560 0 L560 130 L0 130 Z" fill="var(--swoosh)"/>
      <path d="M120 88 C300 68 440 40 560 6" fill="none" stroke="var(--accent)" stroke-width="6"/>
    </svg>
  </section>
</body>
</html>
```